Website development company website

ABOUT COMPANY
Hi everyone! We're a Melbourne, Australia website development company in a need of a website design that will make online store merchants want to engage our services.
We specialise exclusively in Torvista e-commerce platform (https://torvista-platform.example/). What distinguishes our business from competition is that rather than designing and building brand new websites, we offer development, support and maintenance services to established websites. Maintenance and Support are the keywords representing our business.
Our potential clients are people with broken, slow and underperforming Torvista installations who need assistance getting their websites up and making sales. Our website must pass the message that we can help, and provide quick means of making contact.
DESIGN
Overall, we're looking for a slick, clean, airy, conservative design. No need to do anything crazy, try to stick to what's "standard" in website design these days and make it easy on all of us. The website is unlikely to be updated too often so it needs to look attractive and fresh first time over and after a year, too.
Attached is our new logo, which you'll be able to take the basic idea from, the colors and fonts. Though, don't use the fonts from the logo in the website, stick to the standard widely supported fonts. Additional use of Google fonts is fine.
Don't overdo it with colors, stick to conservative basic color set and only use the colors from the log for accents like headings etc. Please, don't be tempted to use the blue and orange as background of whole blocks, other than perhaps footer. Thanks.
For the images used, I'd like to stay away from a design studio/digital agency feel and lean more towards professional support and maintenance services. I'm thinking images of content merchants doing their job. Something along the lines of "We'll be taking care of the website so that you only need to care about the business".
Some ideas I like:
http://www.plumframe-pics.example/detail/photo/portrait-of-confident-male-design-professional-royalty-free-image/572048163
http://www.plumframe-pics.example/detail/photo/designer-taking-picture-of-hat-high-res-stock-photography/839207514
http://www.plumframe-pics.example/detail/photo/woman-packaging-pottery-royalty-free-image/216684093
Images of colorful shopping bags and shopping carts are over the top and not serious enough. Instead of images matching Online Shopping, I'd try going more for Stability, Reliability, Performance.
Our existing website is http://www.bravuln.example. Please, don't take design ideas from it, but it will give you a picture of the structure of our new website and content that's going to be used initially.
If you could include a basic icon set to use throughout the website, that would be great. If the icons could match our logo (attached), it would be a big plus.
ALL PAGES
Every page must contain clearly visible phone number (1300 648 907) and a Contact Us Now button, which opens an AJAX driven popup form with Name, Email, Phone and Message to be sent through.
To start with, main menu items will be Torvista, Portfolio, Contact.
At the bottom of each page, please, include a newsletter subscription form with text Subscribe to Torvista Support and Security Updates.
For the footer, I'd like to see a logo strip with the following logos in grayscale (no need to link anywhere): Torvista, QRX, DataVane, NCB. You'll find the logos on Google Images.
Standard footer columns follow. Here, I'd like to see logos in color: Torvista Certified Developer, Torvista Ceritified Solution Provider. Again, the logos are on Google Images.
No social media logos/links necessary anywhere on the website.
...and then the copyright line.
FRONT PAGE
Large slider with images that would appeal to our target audience. Keywords here would be Torvista System Audit, Torvista Performance Optimisation, Torvista Website Emergency Recovery, Torvista Development Infrastructure Hosting. We'll have a static page created for each of these to link to.
In a corner of the slider, or on the edge, can I have an overlay with logos in color (same as footer): Torvista Certified Developer, Torvista Ceritified Solution Provider.
Underneath, a number of blocks, each with an image and teaser that we'll use to link to various pages throughout the website.
PORTFOLIO PAGE
I'm thinking a single long page with a block per client, which will contain project name, description from us and a testimonial from client. Also, each block will contain a single large screenshot. No gallery or slideshow is necessary here, just one image per project.
I'll leave the layout up to you, but try to put yourself in the shoes of a potential client reviewing our past work by simply scrolling down this one page.
CONTACT US PAGE
Separate page with the same form as above, phone number (1300 648 907), email address (support@kavreo.example), address (Suite 42, Level 3|8 Wattlebrook Lane|Fernvale Heights VIC 3999), and a grayscale Google Map.
CODING UP
Coding up into static HTML/CSS/JS is equally important as the design itself. We're a website development company, we'll be integrating the theme. We will spot any issues and we will point them out.
Coded up design must be fully responsive. Enough said.
To be able to create any content in future, we'd like one extra page coded up with samples of all themed elements, lists, forms, buttons, 2, 3, 4-column layout, alerts, icons, etc. This page does not need to be designed, only coded up.
The design will be integrated into Drupal using Twig. If possible at all, try to keep it in mind when designing and coding up, and make the integration into a Drupal theme easier for us.
GOOD LUCK!
That's it. Let me know if anything needs clarifying. So far I've had a great experience with ArtFlockly. I don't doubt some great designs will emerge. Clever ideas are highly appreciated, but also make it clear you've read and followed the points in this brief. Cheers, Tom

```html
<!DOCTYPE html>
<html lang="en">
<head>
<meta charset="utf-8">
<title>Kavreo E-Commerce – Torvista Development, Support and Maintenance</title>
<link rel="stylesheet" href="https://fonts.googleapis.com/css2?family=Lato:ital,wght@0,400;0,700;1,400&family=Ubuntu:wght@500;700&display=swap">
<style>
:root{
  --orange:#e8661a;
  --orange-band:#e8832a;
  --orange-dark:#b94a0c;
  --navy:#123f6e;
  --logo-blue:#1b4f8c;
  --ink:#1b1b1b;
  --text:#444;
  --white:#fff;
  --strip:#3a3a3a;
  --footer:#0b0b0b;
  --copy:#1c1c1c;
  --rule:#2a2a2a;
}
*{box-sizing:border-box;margin:0;padding:0}
html,body{width:1200px;height:2744px;overflow:hidden}
body{position:relative;background:var(--white);font-family:"Lato",Arial,sans-serif;color:var(--text)}
.abs{position:absolute}

/* header */
.site-header{position:absolute;left:0;top:0;width:1200px;height:92px;background:var(--white);border-top:5px solid var(--orange)}
.brand-mark{position:absolute;left:100px;top:20px;display:flex;align-items:center;gap:10px;font-family:"Ubuntu",sans-serif;font-weight:700;font-size:40px;color:var(--logo-blue)}
.brand-mark .sq{width:16px;height:16px;background:var(--orange)}
.site-title{position:absolute;left:353px;top:22px;font-family:"Ubuntu",sans-serif;font-weight:700;font-size:36px;color:var(--ink)}
.main-nav{position:absolute;left:612px;top:33px;display:flex;align-items:center;font-size:14px;color:#555}
.main-nav a{color:#555;text-decoration:none}
.main-nav a.active{color:var(--navy);font-weight:700}
.main-nav .dot{width:6px;height:6px;border-radius:50%;background:#ccc;margin:0 26px}

/* plain divider mark */
.divider{position:absolute;width:10px;height:10px;background:var(--orange)}
.divider.light{background:var(--white)}

/* hero */
.hero{position:absolute;left:0;top:92px;width:1200px;height:488px;background:linear-gradient(120deg,#d8dde2 0%,#9aa5b2 35%,#5e6b7a 60%,#c9c3bc 100%)}
.hero-caption{position:absolute;left:0;right:0;top:300px;text-align:center;font-family:"Ubuntu",sans-serif;font-weight:500;font-size:27px;color:var(--white);letter-spacing:.3px}
.hero-caption span{background:rgba(120,90,60,.28);padding:4px 12px}
.slide-arrow{position:absolute;width:32px;height:32px;border-radius:3px;background:rgba(255,240,225,.85);display:flex;align-items:center;justify-content:center}

/* technology strip */
.tech-strip{position:absolute;left:0;width:1200px}
.tech-strip span{position:absolute;top:50%;transform:translate(-50%,-50%);font-family:"Ubuntu",sans-serif;font-weight:700;font-size:30px;color:var(--white)}
.tech-strip.top{top:580px;height:113px;background:rgba(40,40,40,.88)}
.tech-strip.bottom{top:2301px;height:117px;background:var(--strip)}

/* feature cards */
.feature{position:absolute;top:693px;width:600px;height:353px;color:var(--white);text-align:center}
.feature.left{left:0;background:linear-gradient(135deg,#4a5866,#2a3440 60%,#56636f)}
.feature.right{left:600px;background:linear-gradient(135deg,#6d7985,#3a4552 55%,#262f3a)}
.feature .shade{position:absolute;inset:0;background:rgba(20,35,55,.45)}
.feature h3{position:absolute;left:0;right:0;font-family:"Ubuntu",sans-serif;font-weight:700;font-size:22px}
.feature p{position:absolute;left:0;right:0;font-size:12.5px;color:#ddd}
.feature a{position:absolute;left:0;right:0;font-size:13px;font-weight:700;color:var(--white);text-decoration:none}

/* section headings */
.section-title{position:absolute;left:0;width:1200px;text-align:center;font-family:"Ubuntu",sans-serif;font-weight:700;font-size:31px;color:var(--ink)}
.section-title em{font-style:normal;color:var(--orange)}
.section-title.on-orange{color:var(--white)}

/* services */
.service{position:absolute;top:1192px;width:300px;text-align:center}
.service .ring{width:110px;height:110px;border:3px solid var(--orange);border-radius:50%;margin:0 auto;display:flex;align-items:center;justify-content:center}
.service h4{margin-top:20px;font-family:"Ubuntu",sans-serif;font-weight:700;font-size:18px;color:var(--navy)}
.service p{margin-top:10px;font-size:13.5px;line-height:20px;color:#444}
.btn-more{display:inline-block;margin-top:16px;width:120px;height:33px;line-height:33px;border-radius:17px;background:var(--orange);box-shadow:4px 2px 0 var(--orange-dark);font-size:14px;font-weight:700;color:var(--white);text-decoration:none}

/* portfolio */
.portfolio{position:absolute;left:0;top:1511px;width:1200px;height:424px;background:var(--orange-band)}
.shot{position:absolute;top:126px;width:233px;height:256px;border:2px solid rgba(255,255,255,.6)}
.side-arrow{position:absolute}

/* testimonials */
.avatar{position:absolute;left:552px;top:2068px;width:96px;height:96px;border-radius:50%;border:4px solid var(--orange);background:linear-gradient(160deg,#dfe6ee,#9fb0c2)}
.client-name{position:absolute;left:0;width:1200px;top:2185px;text-align:center;font-weight:700;font-size:17px;color:var(--navy)}
.quote{position:absolute;left:160px;width:880px;top:2216px;text-align:center;font-style:italic;font-size:13px;line-height:22px;color:#666}

/* footer */
.site-footer{position:absolute;left:0;top:2418px;width:1200px;height:274px;background:var(--footer);color:#ccc}
.footer-col{position:absolute;top:58px}
.footer-col h5{font-family:"Ubuntu",sans-serif;font-weight:700;font-size:17px;color:var(--white);padding-bottom:14px;border-bottom:1px solid var(--rule)}
.quick-links{list-style:none;margin-top:12px;font-size:12.5px}
.quick-links li{height:27.5px;display:flex;align-items:center;gap:10px;color:#ddd}
.quick-links li.current{color:var(--orange)}
.quick-links li::before{content:"›";color:#888;font-size:13px}
.address-line{display:flex;gap:14px;margin-top:14px;font-size:12.5px;line-height:18px;color:#ddd}
.address-line svg{flex:none;margin-top:2px}
.field{width:201px;height:26px;background:var(--white);border:1px solid #ccc;font-size:11.5px;color:#555;padding:5px 7px;margin-top:6px}
.field.message{height:42px}
.btn-submit{margin-top:10px;width:77px;height:26px;background:var(--orange);color:var(--white);font-size:11.5px;font-weight:700;display:flex;align-items:center;justify-content:center}
.map{margin-top:22px;width:247px;height:88px;background:linear-gradient(135deg,#e9e6df,#d6d3cb)}
.copyright{position:absolute;left:0;top:2692px;width:1200px;height:52px;background:var(--copy);color:#ccc;font-size:12px;display:flex;align-items:center;justify-content:center}
</style>
</head>
<body>

<header class="site-header">
  <div class="brand-mark"><span>Kavreo</span><span class="sq"></span></div>
  <div class="site-title">Kavreo</div>
  <nav class="main-nav">
    <a class="active">Home</a><span class="dot"></span>
    <a>About Us</a><span class="dot"></span>
    <a>Torvista</a><span class="dot"></span>
    <a>Portfolio</a><span class="dot"></span>
    <a>Contact Us</a>
  </nav>
  <span class="divider" style="left:634px;top:62px"></span>
</header>

<section class="hero" role="img" aria-label="Photograph of business professionals smiling together around a laptop in an office">
  <div class="hero-caption"><span>High performance Torvista &nbsp;sites on time and on budget.</span></div>
  <div class="slide-arrow" style="left:39px;top:269px"><svg width="12" height="12" viewBox="0 0 12 12"><path d="M8 2 3 6l5 4z" fill="#e8832a"/></svg></div>
  <div class="slide-arrow" style="left:1128px;top:269px"><svg width="12" height="12" viewBox="0 0 12 12"><path d="M4 2l5 4-5 4z" fill="#e8832a"/></svg></div>
</section>

<div class="tech-strip top">
  <span style="left:155px">Markup5</span>
  <span style="left:357px">Torvista</span>
  <span style="left:561px">Brewla</span>
  <span style="left:695px">QRX</span>
  <span style="left:843px">NCB</span>
  <span style="left:1015px">DataVane</span>
</div>

<article class="feature left" role="img" aria-label="Photograph of a desk with laptop, glasses and printed charts">
  <div class="shade"></div>
  <h3 style="top:137px">Torvista Certified Developer</h3>
  <p style="top:170px">Lorem ipsum dolor sit amet, consectetuer adipiscing elit.</p>
  <a style="top:200px">Read More &gt;&gt;</a>
</article>
<article class="feature right" role="img" aria-label="Photograph of a smiling businessman using a tablet">
  <div class="shade"></div>
  <h3 style="top:144px">Torvista Certified Solution Provider</h3>
  <p style="top:177px">Ut wisi enim ad minim veniam, quis nostrud exerci tation</p>
  <a style="top:207px">Read More &gt;&gt;</a>
</article>

<h2 class="section-title" style="top:1085px">Our <em>Services</em></h2>
<span class="divider" style="left:595px;top:1152px"></span>

<div class="service" style="left:104px">
  <div class="ring"><svg width="62" height="44" viewBox="0 0 62 44"><rect x="16" y="2" width="44" height="30" rx="2" fill="none" stroke="#111" stroke-width="3"/><path d="M30 40h16M38 32v8" stroke="#111" stroke-width="3"/><rect x="2" y="12" width="18" height="30" rx="3" fill="#fff" stroke="#111" stroke-width="3"/><circle cx="11" cy="37" r="1.5" fill="#111"/></svg></div>
  <h4>Web development</h4>
  <p>Lorem ipsum dolor sit amet, consectetuer adipiscing &nbsp;elit, sed diam nonummy nibh euismod tincidunt ut &nbsp;lore ipsum</p>
  <a class="btn-more">Read More</a>
</div>
<div class="service" style="left:454px">
  <div class="ring"><svg width="52" height="52" viewBox="0 0 52 52"><path d="M10 24a16 16 0 0 1 32 0" fill="none" stroke="#111" stroke-width="3"/><rect x="7" y="22" width="7" height="12" rx="2" fill="#111"/><rect x="38" y="22" width="7" height="12" rx="2" fill="#111"/><path d="M6 50c2-10 10-14 20-14s18 4 20 14z" fill="#111"/><circle cx="40" cy="40" r="8" fill="#111" stroke="#fff" stroke-width="2"/><text x="40" y="44" font-size="11" font-family="Arial" font-weight="700" fill="#fff" text-anchor="middle">?</text></svg></div>
  <h4>Web support</h4>
  <p>Lorem ipsum dolor sit amet, consectetuer adipiscing &nbsp;elit, sed diam nonummy nibh euismod tincidunt ut &nbsp;lore ipsum</p>
  <a class="btn-more">Read More</a>
</div>
<div class="service" style="left:796px">
  <div class="ring"><svg width="54" height="54" viewBox="0 0 54 54"><path d="M8 46 34 20" stroke="#111" stroke-width="6" stroke-linecap="round"/><path d="M30 12a10 10 0 0 0 12 12l4-4-6-2-2-6 4-4a10 10 0 0 0-12 4z" fill="#111"/><path d="M10 8l6 6M16 14l28 28" stroke="#111" stroke-width="5" stroke-linecap="round"/><path d="M40 38l8 8" stroke="#111" stroke-width="8" stroke-linecap="round"/></svg></div>
  <h4>Web maintenance</h4>
  <p>Lorem ipsum dolor sit amet, consectetuer adipiscing &nbsp;elit, sed diam nonummy nibh euismod tincidunt ut &nbsp;lore ipsum</p>
  <a class="btn-more">Read More</a>
</div>

<section class="portfolio">
  <h2 class="section-title on-orange" style="top:34px">Our Portfolio</h2>
  <span class="divider light" style="left:595px;top:88px"></span>
  <svg class="side-arrow" style="left:56px;top:234px" width="16" height="28" viewBox="0 0 16 28"><path d="M14 2 3 14l11 12" fill="none" stroke="rgba(255,255,255,.7)" stroke-width="2"/></svg>
  <svg class="side-arrow" style="left:1126px;top:234px" width="16" height="28" viewBox="0 0 16 28"><path d="M2 2l11 12L2 26" fill="none" stroke="rgba(255,255,255,.7)" stroke-width="2"/></svg>
  <div class="shot" style="left:108px;background:linear-gradient(180deg,#1d2a3e 0%,#2f6f9a 25%,#1d2a3e 45%,#243449 100%)" role="img" aria-label="Screenshot of a dark blue business website template"></div>
  <div class="shot" style="left:358px;background:linear-gradient(180deg,#3b4a2c 0%,#5d6b3a 55%,#8a8a8a 75%,#9a9a9a 100%)" role="img" aria-label="Screenshot of a landing page template with a hover magnifier"></div>
  <div class="shot" style="left:609px;background:linear-gradient(180deg,#8cc63e 0%,#b9dc6a 30%,#f3f3f3 45%,#ffffff 100%)" role="img" aria-label="Screenshot of a green software company website template"></div>
  <div class="shot" style="left:860px;background:linear-gradient(180deg,#52c3c7 0%,#7fd6d2 45%,#ffffff 55%,#f4f4f4 100%)" role="img" aria-label="Screenshot of a personal portfolio page for a designer"></div>
</section>

<h2 class="section-title" style="top:1979px">Client <em>Testimonials</em></h2>
<span class="divider" style="left:595px;top:2036px"></span>
<svg class="abs" style="left:112px;top:2104px" width="16" height="24" viewBox="0 0 16 24"><path d="M13 2 3 12l10 10" fill="none" stroke="#aaa" stroke-width="4"/></svg>
<svg class="abs" style="left:1066px;top:2104px" width="16" height="24" viewBox="0 0 16 24"><path d="M3 2l10 10L3 22" fill="none" stroke="#aaa" stroke-width="4"/></svg>
<div class="avatar" role="img" aria-label="Portrait photograph of the client"></div>
<div class="client-name">Vestibulum porta</div>
<p class="quote">Lorem ipsum dolor sit amet, consectetur adipiscing elit. Integer venenatis tincidunt elit, aliquam semper quam pulvinar id. Aliquam erat volutpat. Integer nulla urna, sagittis sed viverra quis, tincidunt vel felis. Pellentesque eleifend sem ut diam bibendum, non sagittis sapien pellentesque. Etiam semper</p>

<div class="tech-strip bottom">
  <span style="left:155px">Markup5</span>
  <span style="left:357px">Torvista</span>
  <span style="left:561px">Brewla</span>
  <span style="left:695px">QRX</span>
  <span style="left:843px">NCB</span>
  <span style="left:1015px">DataVane</span>
</div>

<footer class="site-footer">
  <div class="footer-col" style="left:104px;width:110px">
    <h5>Quick Links</h5>
    <ul class="quick-links">
      <li class="current">Home</li><li>About Us</li><li>Torvista</li><li>Portfolio</li><li>Contact Us</li>
    </ul>
  </div>
  <div class="footer-col" style="left:293px;width:190px">
    <h5>Address</h5>
    <div class="address-line"><svg width="12" height="16" viewBox="0 0 12 16"><path d="M6 0a6 6 0 0 1 6 6c0 4-6 10-6 10S0 10 0 6a6 6 0 0 1 6-6z" fill="#fff"/><circle cx="6" cy="6" r="2.2" fill="#0b0b0b"/></svg><span>Kavreo E-Commerce<br>Suite 42, Level 3|8 Wattlebrook Lane| Fernvale Heights VIC 3999</span></div>
    <div class="address-line" style="margin-top:16px"><svg width="13" height="13" viewBox="0 0 13 13"><path d="M2 0l3 3-1.5 2a8 8 0 0 0 4.5 4.5L10 8l3 3-2 2C5 13 0 8 0 2z" fill="#fff"/></svg><span>123-456-7890</span></div>
    <div class="address-line" style="margin-top:16px"><svg width="13" height="10" viewBox="0 0 13 10"><rect width="13" height="10" fill="#fff"/><path d="M0 0l6.5 5L13 0" fill="none" stroke="#0b0b0b" stroke-width="1.3"/></svg><span>info@kavreo.example</span></div>
  </div>
  <div class="footer-col" style="left:571px;width:230px">
    <h5>Get in Touch</h5>
    <div class="field" style="margin-top:12px">Name</div>
    <div class="field">Email</div>
    <div class="field message">Message</div>
    <div class="btn-submit">SUBMIT</div>
  </div>
  <div class="footer-col" style="left:854px;width:247px">
    <h5>Location Map</h5>
    <div class="map" role="img" aria-label="Street map showing the office location with a red pin"></div>
  </div>
</footer>
<div class="copyright">Copyright © 2016 Kavreo E-Commerce</div>

</body>
</html>
```